Podiatry clinic requires a modern revamp and editing of existing website.

I would like a fresh new look and updated information for my current business website. An easy to navigate site with prominent address and phone number for call to action. We are a podiatry clinic that focuses on general and sports podiatry.
I would like 4 pages; including Home page, About Us, Services & Contact.
www.brambleridgepodiatry.net

Target Market(s)

Active working professionals.

Industry/Entity Type

Medical

Coding

Coded - Design and coding required

Number of Pages Required

4 page

Font styles to use
Sans Serif

Colors
6b449b

Requirements
Must have
• A modern look with logo and active images; clean and uncluttered. Visible phone number and address for call to action.
• 4 pages - Home, About Us, Services, Contact.
• Home page - update address & service logos.
• About Us - update of personal information.
• Services - Revamp of existing page.
• Contact page to include Google map, email & phone number.
Nice to have
• Ability to add content easily; eg. a blog or adding video onto Home page.
• Link to Circlepage page.

```html
<!DOCTYPE html>
<html lang="en">
<head>
<meta charset="utf-8">
<title>Bramble Ridge Podiatry</title>
<link rel="stylesheet" href="https://fonts.googleapis.com/css2?family=Lato:wght@700;900&family=Open+Sans:wght@400;600;700&family=Raleway:wght@400;500&display=swap">
<style>
:root{
  --purple:#6b449b;
  --deep:#46308f;
  --mid:#6a52c4;
  --light:#b9a6dc;
  --green:#7dc142;
  --white:#fff;
  --ink:#555;
  --heading:#4c3596;
}
*{box-sizing:border-box;margin:0;padding:0}
html,body{width:1200px;height:2894px;overflow:hidden}
body{font-family:"Open Sans",sans-serif;color:var(--white);background:#fff;position:relative}
.abs{position:absolute}
a{color:inherit;text-decoration:none}

/* header */
.topbar{left:0;top:0;width:1200px;height:162px;background:linear-gradient(180deg,#9a86c7 0%,#c7b8e4 60%,#b5a3d9 100%)}
.topbar .address{left:77px;top:52px;font-size:15px;line-height:24px;display:flex;gap:12px}
.brand{left:480px;top:14px;width:260px;height:134px;display:flex;align-items:center;gap:12px}
.brand .mark{width:46px;height:46px;border-radius:50%;background:var(--deep);flex:none}
.brand .name{font-family:"Open Sans",sans-serif;font-weight:700;font-size:26px;line-height:32px;color:var(--deep);white-space:nowrap}
.call{left:862px;top:46px;display:flex;gap:16px;align-items:center}
.call .ring{width:52px;height:52px;border:2px solid #fff;border-radius:50%;display:flex;align-items:center;justify-content:center}
.call small{display:block;font-size:18px}
.call strong{font-size:33px;font-weight:700;line-height:38px}

.nav{left:0;top:162px;width:1200px;height:56px;background:var(--deep);display:flex;padding-left:77px}
.nav a{font-family:"Raleway",sans-serif;font-size:19px;line-height:56px;padding:0 34px}
.nav a.active{background:var(--green);width:122px;text-align:center;padding:0}

/* hero */
.hero{left:0;top:218px;width:1200px;height:531px;background:linear-gradient(90deg,#8a7cc8 0%,#a8b6e6 40%,#7dc8ee 70%,#c9e6f5 100%)}
.hero .photo{left:600px;top:0;width:600px;height:531px;background:linear-gradient(200deg,rgba(230,180,150,0) 0%,rgba(225,170,140,.85) 100%)}
.hero h1{left:80px;top:92px;font-family:"Lato",sans-serif;font-weight:900;font-size:46px;line-height:78px}
.hero p{left:80px;top:244px;font-size:21px;line-height:32px;width:360px}
.btn{display:inline-block;border-radius:32px;text-align:center}
.hero .btn{left:78px;top:357px;width:228px;height:60px;line-height:60px;background:var(--deep);font-family:"Raleway",sans-serif;font-size:24px}

/* features */
.feature{top:749px;width:600px;height:260px}
.feature.general{left:0;background:var(--deep)}
.feature.special{left:600px;background:var(--mid)}
.feature .thumb{left:77px;top:32px;width:184px;height:184px;border-radius:50%;border:5px solid #fff;background:linear-gradient(135deg,#e9d6cc,#b9c7d9)}
.feature.special .thumb{left:28px}
.feature h2{font-family:"Raleway",sans-serif;font-weight:400;font-size:27px;left:282px;top:25px}
.feature.special h2{left:233px}
.feature p{font-size:15px;line-height:26px;width:296px;left:282px;top:77px}
.feature.special p{left:233px}
.feature .btn{left:280px;top:173px;width:190px;height:50px;line-height:50px;background:#fff;color:var(--deep);font-family:"Raleway",sans-serif;font-size:22px}
.feature.special .btn{left:231px}

/* welcome */
.welcome-img{left:0;top:1009px;width:155px;height:253px;background:linear-gradient(160deg,#efe1d9,#d9a08c)}
.welcome h2{left:168px;top:1061px;width:1032px;font-family:"Raleway",sans-serif;font-weight:400;font-size:44px;color:#555}
.welcome h2 span{color:var(--heading)}
.welcome p{left:210px;top:1133px;width:800px;text-align:center;font-size:15px;line-height:28px;color:var(--ink)}
.welcome .btn{left:505px;top:1209px;width:190px;height:52px;line-height:52px;background:var(--deep);font-family:"Raleway",sans-serif;font-size:22px}

/* enquiry */
.enquiry{left:77px;top:1327px;width:1046px;height:256px;background:var(--deep);border-bottom:5px solid var(--green);box-shadow:0 30px 40px -20px rgba(0,0,0,.35);text-align:center}
.enquiry .foot{left:60px;top:26px;width:92px;height:190px;border-radius:46px 46px 40px 40px;background:#7b63cf}
.enquiry .hands{left:870px;top:0;width:120px;height:225px;background:linear-gradient(180deg,#e7b79f,#c8896e)}
.enquiry h2{left:0;width:1046px;top:24px;font-family:"Raleway",sans-serif;font-weight:400;font-size:40px}
.enquiry .line{left:0;width:1046px;top:95px;font-family:"Raleway",sans-serif;font-size:30px;display:flex;justify-content:center;align-items:center;gap:12px}
.enquiry .line .ring{width:50px;height:50px;border:2px solid #fff;border-radius:50%;display:flex;align-items:center;justify-content:center}
.enquiry .line strong{font-family:"Open Sans",sans-serif;font-weight:700}
.enquiry .or{left:0;width:1046px;top:160px;font-size:20px}
.enquiry .email{left:0;width:1046px;top:195px;font-size:21px}
.enquiry .notch{left:513px;top:251px}

/* follow & news */
.social{left:0;top:1686px;width:1200px;height:382px;background:var(--mid)}
.social h3{font-family:"Raleway",sans-serif;font-weight:400;font-size:40px;top:45px}
.follow h3{left:80px}
.follow .badge{left:70px;top:120px;width:126px;height:126px;border-radius:50%;background:#fff}
.follow .page-name{left:215px;top:134px;font-family:"Raleway",sans-serif;font-size:31px}
.follow .like{left:215px;top:188px;width:202px;height:62px;background:#fff;border:2px solid #9bb;border-radius:4px;color:var(--deep);display:flex;align-items:center;gap:10px;padding:0 10px;font-weight:600;font-size:20px;line-height:24px}
.follow .like i{width:36px;height:36px;background:var(--deep);flex:none}
.divider{left:600px;top:48px;width:1px;height:280px;background:rgba(255,255,255,.3)}
.news h3{left:640px}
.news .item{left:640px;width:480px;font-size:15px;line-height:26px}
.news .item .date{font-size:14px}
.news .sep{left:640px;top:230px;width:480px;height:1px;background:rgba(255,255,255,.3)}

/* about */
.about{left:0;top:2068px;width:1200px;height:363px;background:var(--deep)}
.about .video{left:77px;top:61px;width:434px;height:239px;background:linear-gradient(135deg,#d8d8d8,#8a8a8a)}
.about .play{left:264px;top:150px}
.about h2{left:545px;top:52px;font-family:"Raleway",sans-serif;font-weight:400;font-size:40px}
.about p{left:545px;width:570px;font-size:15px;line-height:26px}

/* partners */
.partners{left:0;top:2431px;width:1200px;height:155px;background:#fff;display:flex;justify-content:space-around;align-items:center;padding:0 60px}
.partners .shape{height:80px;border-radius:6px}

/* footer */
.footer{left:0;top:2586px;width:1200px;height:254px;background:var(--deep)}
.footer .brand-foot{left:80px;top:44px;display:flex;align-items:center;gap:14px}
.footer .brand-foot i{width:56px;height:56px;border-radius:50%;background:#8f7ad6;flex:none}
.footer .brand-foot span{font-weight:700;font-size:28px;line-height:38px;color:#b9a6e8}
.footer h4{font-family:"Raleway",sans-serif;font-weight:400;font-size:20px;top:32px}
.footer ul{list-style:none;font-size:17px;line-height:37px;top:68px}
.footer .links li::before{content:"\2192";margin-right:12px}
.footer .touch li{display:flex;gap:12px;line-height:26px;margin-bottom:12px}
.footer .follow-foot li{display:flex;align-items:center;gap:12px;margin-bottom:20px;line-height:46px}
.footer .follow-foot li i{width:46px;height:46px;border-radius:50%;border:2px solid #fff}
.copyright{left:0;top:2840px;width:1200px;height:54px;background:#5b40b0;text-align:center;line-height:54px;font-size:15px}
</style>
</head>
<body>

<header class="topbar abs">
  <div class="address abs">
    <svg width="16" height="22" viewBox="0 0 16 22"><path d="M8 0a8 8 0 0 0-8 8c0 6 8 14 8 14s8-8 8-14a8 8 0 0 0-8-8zm0 11a3 3 0 1 1 0-6 3 3 0 0 1 0 6z" fill="#fff"/></svg>
    <span>Suite 12 / 88 Harwick Lane<br>Fernvale 4021</span>
  </div>
  <div class="brand abs"><span class="mark"></span><span class="name">Bramble Ridge<br>Podiatry</span></div>
  <div class="call abs">
    <span class="ring"><svg width="24" height="24" viewBox="0 0 24 24"><path d="M6.6 10.8a15 15 0 0 0 6.6 6.6l2.2-2.2c.3-.3.7-.4 1-.2 1.1.4 2.3.6 3.6.6.6 0 1 .4 1 1V20c0 .6-.4 1-1 1A17 17 0 0 1 3 4c0-.6.4-1 1-1h3.5c.6 0 1 .4 1 1 0 1.2.2 2.4.6 3.6.1.3 0 .7-.2 1z" fill="#fff"/></svg></span>
    <div><small>CALL US NOW!</small><strong>1300 482 907</strong></div>
  </div>
</header>

<nav class="nav abs">
  <a class="active" href="#">HOME</a><a href="#">ABOUT</a><a href="#">SERVICES</a><a href="#">CONTACT</a>
</nav>

<section class="hero abs">
  <div class="photo abs" role="img" aria-label="Photo of bare feet resting against a sunny beach backdrop"></div>
  <h1 class="abs">QUALIFIED HEALTH<br>PROFESSIONALS</h1>
  <p class="abs">Various foot conditions, including Sports Injuries, Orthotic Therapy &amp; Nail Surgery</p>
  <a class="btn abs" href="#">CONTACT US</a>
</section>

<section class="feature general abs">
  <div class="thumb abs" role="img" aria-label="Photo of a podiatrist examining a foot"></div>
  <h2 class="abs">General Treatment</h2>
  <p class="abs">Nails, Corns, Callus, Warts, Skin Disorders, Heel pain / Heel Spurs / Arch pain - plantar Fasciitis</p>
  <a class="btn abs" href="#">READ MORE</a>
</section>
<section class="feature special abs">
  <div class="thumb abs" role="img" aria-label="Photo of a nail treatment on a toe"></div>
  <h2 class="abs">Specialised Treatments</h2>
  <p class="abs">Diabetic Management, Nail Surgery, Biomechanical Assessment, Gait Analysis, Orthotic Therapy</p>
  <a class="btn abs" href="#">READ MORE</a>
</section>

<section class="welcome">
  <div class="welcome-img abs" role="img" aria-label="Photo of hands holding a sore heel"></div>
  <h2 class="abs">WELCOME TO <span>BRAMBLE RIDGE PODIATRY</span></h2>
  <p class="abs">Bramble Ridge Podiatry is a Podiatry clinic in the heart of Fernvale city centre. We are located between Orchard &amp; Tallis Streets in the Harwick Trade Centre / Linden Suites Complex.</p>
  <a class="btn abs" href="#">READ MORE</a>
</section>

<section class="enquiry abs">
  <div class="foot abs"></div>
  <div class="hands abs" role="img" aria-label="Photo of hands cradling a foot"></div>
  <h2 class="abs">For Appointments or Enquiries</h2>
  <div class="line abs">Please call us on
    <span class="ring"><svg width="24" height="24" viewBox="0 0 24 24"><path d="M6.6 10.8a15 15 0 0 0 6.6 6.6l2.2-2.2c.3-.3.7-.4 1-.2 1.1.4 2.3.6 3.6.6.6 0 1 .4 1 1V20c0 .6-.4 1-1 1A17 17 0 0 1 3 4c0-.6.4-1 1-1h3.5c.6 0 1 .4 1 1 0 1.2.2 2.4.6 3.6.1.3 0 .7-.2 1z" fill="#fff"/></svg></span>
    <strong>1300 482 907</strong></div>
  <div class="or abs">OR</div>
  <div class="email abs">Email: &#9993; info@brambleridgepodiatry.net</div>
  <svg class="notch abs" width="20" height="12" viewBox="0 0 20 12"><path d="M0 0h20L10 12z" fill="#7dc142"/></svg>
</section>

<section class="social abs">
  <div class="follow">
    <h3 class="abs">FOLLOW US</h3>
    <div class="badge abs"></div>
    <div class="page-name abs">Bramble Ridge Podiatry</div>
    <a class="like abs" href="#"><i></i><span>Like Us on<br>Circlepage</span></a>
  </div>
  <div class="divider abs"></div>
  <div class="news">
    <h3 class="abs">LATEST NEWS</h3>
    <div class="item abs" style="top:108px">Lorem Ipsum is simply dummy text of the printing.<br><span class="date">&#9638; 01 August 2016</span><br>Lorem Ipsum is simply dummy text of the printing and type setting industry.</div>
    <div class="sep abs"></div>
    <div class="item abs" style="top:240px">Lorem Ipsum is simply dummy text of the printing.<br><span class="date">&#9638; 01 August 2016</span><br>Lorem Ipsum is simply dummy text of the printing and type setting industry.</div>
  </div>
</section>

<section class="about abs">
  <div class="video abs" role="img" aria-label="Video still of a podiatrist treating a foot with clinic tools"></div>
  <svg class="play abs" width="60" height="60" viewBox="0 0 60 60" aria-label="Play video"><circle cx="30" cy="30" r="27" fill="rgba(70,48,143,.55)" stroke="#fff" stroke-width="3"/><path d="M24 18l18 12-18 12z" fill="#fff"/></svg>
  <h2 class="abs">ABOUT PODIATRISTS</h2>
  <p class="abs" style="top:122px">Our podiatrists are fully qualified health professionals who are able to diagnose, treat, manage or help to prevent all medical conditions that affect the feet and lower limb.</p>
  <p class="abs" style="top:212px">We provide General Podiatry Treatment and some Specialised Services in relation to various foot conditions, including Sports Injuries, Orthotic Therapy and Nail Surgery.</p>
</section>

<section class="partners abs">
  <div class="shape" style="width:190px;background:#3b5bab"></div>
  <div class="shape" style="width:240px;height:30px;background:#333"></div>
  <div class="shape" style="width:215px;height:54px;background:#1ea84f"></div>
  <div class="shape" style="width:210px;background:#1f5fae"></div>
</section>

<footer class="footer abs">
  <div class="brand-foot abs"><i></i><span>Bramble<br>Ridge<br>Podiatry</span></div>
  <h4 class="abs" style="left:350px">Useful Links</h4>
  <ul class="links abs" style="left:350px"><li>Home</li><li>About</li><li>Services</li><li>Contact</li></ul>
  <h4 class="abs" style="left:622px">Get In Touch</h4>
  <ul class="touch abs" style="left:622px;width:250px">
    <li><span>&#9679;</span><span>Suite 12 / 88 Harwick Lane<br>Fernvale 4021</span></li>
    <li><span>&#9742;</span><strong>1300 482 907</strong></li>
    <li><span>&#9993;</span><span>info@brambleridgepodiatry.<br>net</span></li>
  </ul>
  <h4 class="abs" style="left:892px">Follow Us</h4>
  <ul class="follow-foot abs" style="left:888px"><li><i></i>Circlepage</li><li><i></i>Chirpline</li></ul>
</footer>
<div class="copyright abs">&copy; Bramble Ridge Podiatry- 2016. All Rights Reserved.</div>

</body>
</html>
```